Black Matte card with samurai logo which I would like it to be textured and company name on one side and on the other side I would like the company information with the reno (Face logo) Sushi logo. Double Sided card.

majority customers are University students, University sororities and fraternities.

It Company

Reno Sushi
317 W. Harlow Ave
Tucson, AZ 85042
Phone (520)413-6271
Fax (520)357-1846
E-mail: Renosushidesert@mailbox-example.com
FB: Renosushidesert
Twitter: Renosushidesert

• Present Normal

```html
<!DOCTYPE html>
<html lang="en">
<head>
<meta charset="utf-8">
<title>Reno Sushi – Business Card</title>
<link rel="stylesheet" href="https://fonts.googleapis.com/css2?family=Source+Sans+3:wght@400&display=swap">
<style>
  :root {
    --bg: #e6e1d8;
    --card-black: #0c0c0c;
    --card-black-light: #2a2a2a;
    --card-white: #ffffff;
    --brand-red: #e0242f;
    --deep-red: #b5342a;
    --ink: #4a4a4a;
    --rule: #c9c9c9;
    --band-black: #1d1d1d;
    --social: #5a6f9e;
  }
  * { margin: 0; padding: 0; box-sizing: border-box; }
  html, body {
    width: 1200px; height: 1102px; overflow: hidden;
    background: var(--bg);
    font-family: "Source Sans 3", Arial, sans-serif;
  }
  .canvas { position: relative; width: 1200px; height: 1102px; }

  .card { position: absolute; width: 856px; height: 489px; box-shadow: 0 3px 10px rgba(0,0,0,.25); overflow: hidden; }

  /* Front */
  .card-front {
    left: 33px; top: 50px;
    background: radial-gradient(ellipse at 50% 30%, var(--card-black-light) 0%, var(--card-black) 70%);
  }
  .card-front .texture {
    position: absolute; inset: 0;
    background-image:
      repeating-linear-gradient(0deg, rgba(255,255,255,.03) 0 1px, transparent 1px 3px),
      repeating-linear-gradient(90deg, rgba(255,255,255,.025) 0 1px, transparent 1px 4px);
  }
  .front-name {
    position: absolute; left: 0; right: 0; top: 228px;
    text-align: center;
    color: var(--brand-red); font-size: 80px; line-height: 1; white-space: nowrap;
  }

  /* Back */
  .card-back { left: 299px; top: 584px; background: var(--card-white); border: 1px solid #d4d4d4; }
  .back-name {
    position: absolute; left: 40px; top: 272px; width: 300px;
    text-align: center;
    color: var(--deep-red); font-size: 58px; line-height: 1;
  }
  .divider { position: absolute; left: 371px; top: 109px; width: 1px; height: 272px; background: var(--rule); }

  .contact-list { position: absolute; left: 400px; top: 124px; list-style: none; }
  .contact-list li {
    display: flex; align-items: center; height: 32.5px;
    font-size: 21px; color: var(--ink); white-space: nowrap;
  }
  .contact-list svg { width: 18px; height: 18px; margin-right: 10px; flex: none; }
  .address { position: absolute; left: 400px; top: 312px; font-size: 21px; line-height: 30px; color: var(--ink); }

  .band { position: absolute; left: 0; bottom: 0; width: 100%; height: 22px; }
</style>
</head>
<body>
<div class="canvas">

  <section class="card card-front" aria-label="Card front">
    <div class="texture"></div>
    <p class="front-name">reno sushi</p>
  </section>

  <section class="card card-back" aria-label="Card back">
    <p class="back-name">reno sushi</p>
    <div class="divider"></div>

    <ul class="contact-list">
      <li>
        <svg viewBox="0 0 20 20"><circle cx="10" cy="10" r="8.5" fill="none" stroke="var(--deep-red)" stroke-width="1.6"/><path d="M7 5.5l2 2.3-1 1.2a6 6 0 0 0 3 3l1.2-1 2.3 2-1.2 1.5C10 14 6 10 5.5 6.8z" fill="var(--deep-red)"/></svg>
        (520)413-6271
      </li>
      <li>
        <svg viewBox="0 0 20 20"><rect x="5" y="2" width="10" height="16" rx="2" fill="var(--deep-red)"/><rect x="7" y="4.5" width="6" height="5" fill="#fff"/><rect x="7" y="11.5" width="6" height="4" fill="#fff" opacity=".6"/></svg>
        (520)357-1846
      </li>
      <li>
        <svg viewBox="0 0 20 20"><rect x="2" y="5" width="16" height="11" rx="1" fill="var(--deep-red)"/><path d="M2.5 5.5L10 11l7.5-5.5" fill="none" stroke="#fff" stroke-width="1.5"/></svg>
        Renosushidesert@mailbox-example.com
      </li>
      <li>
        <svg viewBox="0 0 20 20"><rect x="2" y="2" width="16" height="16" rx="2" fill="var(--social)"/></svg>
        Renosushidesert
      </li>
      <li>
        <svg viewBox="0 0 20 20"><rect x="2" y="2" width="16" height="16" rx="2" fill="var(--social)" opacity=".7"/></svg>
        Renosushidesert
      </li>
    </ul>

    <p class="address">Reno Sushi 317 W. Harlow Ave Tucson<br>AZ 85042</p>

    <svg class="band" viewBox="0 0 856 22" preserveAspectRatio="none" aria-hidden="true">
      <polygon points="0,0 340,0 318,22 0,22" fill="var(--band-black)"/>
      <polygon points="362,0 856,0 856,22 340,22" fill="var(--deep-red)"/>
    </svg>
  </section>

</div>
</body>
</html>
```